wealth management firm, professional group, new model

we have a logo that works but we need a card, white background using our colors...clean look

our tag line if can be used in

Your Path From Investor to Partner

```html
<!DOCTYPE html>
<html lang="en">
<head>
<meta charset="utf-8">
<title>Arvel Capital – Business Card</title>
<link href="https://fonts.googleapis.com/css2?family=Montserrat:wght@400;500;700&display=swap" rel="stylesheet">
<style>
  :root {
    --navy: #172c4f;
    --ink: #111111;
    --paper: #ffffff;
    --backdrop: #1f1f1f;
  }
  * { margin: 0; padding: 0; box-sizing: border-box; }
  html, body {
    width: 1200px; height: 1059px; overflow: hidden;
    background: var(--backdrop);
    font-family: "Montserrat", Arial, sans-serif;
  }
  .stage { position: relative; width: 1200px; height: 1059px; }

  .card {
    position: absolute; left: 249px; width: 702px; height: 401px;
    border-radius: 24px; overflow: hidden;
  }
  .card-front { top: 80px; background: var(--paper); }
  .card-back { top: 546px; background: var(--navy); }

  .brand {
    position: absolute; left: 388px; width: 300px; top: 104px;
    text-align: center; color: var(--navy);
    font-size: 30px; font-weight: 500; line-height: 1; white-space: nowrap;
  }

  .person { position: absolute; left: 28px; top: 200px; }
  .person-name { font-size: 29px; font-weight: 700; color: var(--navy); letter-spacing: 0.3px; line-height: 1; }
  .person-title { font-size: 19px; font-weight: 400; color: var(--ink); margin-top: 9px; line-height: 1.2; }

  .rule { position: absolute; left: 28px; width: 619px; top: 267px; height: 1.5px; background: var(--ink); }

  .contacts { position: absolute; left: 24px; top: 283px; list-style: none; color: var(--ink); font-size: 16.5px; }
  .contacts li { display: flex; align-items: center; height: 26px; }
  .contacts li + li { margin-top: 2px; }
  .contacts svg { width: 24px; height: 22px; margin-right: 13px; flex: none; }

  .address {
    position: absolute; right: 55px; top: 312px; text-align: right;
    font-size: 16.5px; line-height: 23px; color: var(--ink); font-style: normal;
  }

  .band { position: absolute; left: 0; bottom: 0; width: 702px; height: 20px; }

  .back-brand {
    position: absolute; left: 0; right: 0; top: 170px; text-align: center;
    color: var(--paper); font-size: 44px; font-weight: 500; line-height: 1;
  }
  .tagline {
    position: absolute; left: 0; right: 0; top: 311px; text-align: center;
    color: var(--paper); font-size: 23px; font-weight: 400;
  }
</style>
</head>
<body>
<main class="stage">
  <section class="card card-front">
    <div class="brand">ARVEL CAPITAL</div>

    <div class="person">
      <h1 class="person-name">DANIEL MOORE</h1>
      <p class="person-title">MANAGING DIRECTOR</p>
    </div>

    <div class="rule"></div>

    <ul class="contacts">
      <li>
        <svg viewBox="0 0 24 24" aria-hidden="true"><path fill="#172c4f" d="M6.6 10.8c1.4 2.8 3.8 5.1 6.6 6.6l2.2-2.2c.3-.3.7-.4 1-.2 1.1.4 2.3.6 3.6.6.6 0 1 .4 1 1V20c0 .6-.4 1-1 1C10.6 21 3 13.4 3 4c0-.6.4-1 1-1h3.5c.6 0 1 .4 1 1 0 1.3.2 2.5.6 3.6.1.3 0 .7-.2 1z"/></svg>
        044-987 650 321
      </li>
      <li>
        <svg viewBox="0 0 24 20" aria-hidden="true"><rect x="1" y="3" width="22" height="15" fill="#172c4f"/><path d="M2 4l10 7.5L22 4" fill="none" stroke="#ffffff" stroke-width="1.6"/></svg>
        info@arvelcapital.com
      </li>
      <li>
        <svg viewBox="0 0 24 24" aria-hidden="true"><circle cx="12" cy="12" r="9.5" fill="none" stroke="#172c4f" stroke-width="2"/><path fill="#172c4f" d="M7 6c2 1 3 3 2 5s1 3 2 4-1 3-2 4c-2.5-1.5-4.5-4-4.5-7S5.5 7 7 6zM14 4.5c3 1 4.8 3 5.3 5.5-2 0-3-.5-4 .5s0 3-1 4-2 0-2-2 1-3 0-4 0-3 1.7-4z"/></svg>
        www.arvelcapital.com
      </li>
    </ul>

    <address class="address">
      421, Address line goes here<br>
      45452, Country name
    </address>

    <svg class="band" viewBox="0 0 702 20" preserveAspectRatio="none" aria-hidden="true">
      <polygon points="0,5 702,2 702,20 0,20" fill="#172c4f"/>
      <polygon points="333,20 362,4 368,4 341,20" fill="#ffffff"/>
    </svg>
  </section>

  <section class="card card-back">
    <div class="back-brand">ARVEL CAPITAL</div>
    <p class="tagline">Your Path From Investor to Partner</p>
  </section>
</main>
</body>
</html>
```